Business Card Design for Marketing Firm

Looking for business card design for higher end marketing firm. Clean but impressionable/trendy. We are a marketing firm that represents manufacturers in the foodservice equipment and supply industry. Our customers are end users such has hotels, restaurants, country clubs, convention centers and casinos as well as distributors of restaurants supplies and equipment, and manufacturers of foodservice equipment and supplies.
Target Market(s)
Hotels, Restaurants, Supply & Equipment Distributors, Foodservice Manufacturers
Industry/Entity Type
Foodservice/Hospitality
Contact Information for Business Card
Name, Title, Contact Number, Email, Website, Social Media, Address
Requirements
Must have
- Clean & Simple but Serious and Impressionable

```html
<!DOCTYPE html>
<html lang="en">
<head>
<meta charset="utf-8">
<title>Meridian Hospitality Reps – Business Card</title>
<link rel="stylesheet" href="https://fonts.googleapis.com/css2?family=Cinzel:wght@500&family=Tinos:wght@700&family=Arimo:wght@400&display=swap">
<style>
  :root {
    --navy: #0b0c8a;
    --navy-deep: #07086e;
    --paper: #f7f7f9;
    --white: #ffffff;
    --stage: #e4e5ea;
  }
  * { box-sizing: border-box; margin: 0; padding: 0; }
  html, body { width: 1200px; height: 768px; overflow: hidden; }
  body {
    background: var(--stage);
    display: flex;
    align-items: center;
    justify-content: center;
    gap: 40px;
  }
  .card {
    position: relative;
    width: 540px;
    height: 309px;
    border-radius: 18px;
    overflow: hidden;
    box-shadow: 0 6px 18px rgba(0,0,0,.18);
  }
  /* Back side */
  .card-back {
    background: var(--navy);
    display: flex;
    align-items: center;
    justify-content: center;
  }
  .back-wordmark {
    font-family: "Cinzel", serif;
    font-weight: 500;
    font-size: 30px;
    letter-spacing: 2px;
    color: var(--white);
    text-align: center;
    line-height: 1.3;
  }
  /* Front side */
  .card-front { background: var(--paper); }
  .front-wave { position: absolute; inset: 0; }
  .brand {
    position: absolute;
    left: 40px;
    top: 62px;
    width: 260px;
    font-family: "Cinzel", serif;
    font-weight: 500;
    color: var(--navy);
  }
  .brand-name {
    font-size: 19px;
    letter-spacing: 1px;
    border-bottom: 1.5px solid var(--navy);
    padding-bottom: 3px;
    white-space: nowrap;
  }
  .brand-sub {
    font-size: 19px;
    letter-spacing: 1px;
    text-align: right;
    margin-top: 1px;
  }
  .social {
    position: absolute;
    right: 30px;
    top: 74px;
    display: flex;
    gap: 6px;
  }
  .social-dot {
    width: 20px; height: 20px;
    border-radius: 50%;
    background: var(--navy-deep);
  }
  .contact {
    position: absolute;
    right: 28px;
    top: 170px;
    list-style: none;
    font-family: "Arimo", sans-serif;
    font-size: 12px;
    color: var(--white);
    text-align: right;
    line-height: 15px;
  }
  .contact li { display: flex; justify-content: flex-end; align-items: center; gap: 8px; white-space: nowrap; }
  .contact .icon { width: 11px; height: 11px; flex: none; }
  .contact .no-icon { padding-right: 19px; }
  .person {
    position: absolute;
    right: 47px;
    bottom: 12px;
    text-align: right;
    color: var(--white);
    line-height: 1.15;
  }
  .person-name {
    font-family: "Tinos", serif;
    font-weight: 700;
    font-size: 21px;
    letter-spacing: 1px;
  }
  .person-title {
    font-family: "Arimo", sans-serif;
    font-size: 13px;
  }
</style>
</head>
<body>
  <section class="card card-back" aria-label="Card back">
    <p class="back-wordmark">Meridian<br>Hospitality Reps</p>
  </section>

  <section class="card card-front" aria-label="Card front">
    <svg class="front-wave" viewBox="0 0 540 309" preserveAspectRatio="none" aria-hidden="true">
      <path d="M0,150 C60,230 150,258 250,240 C300,230 370,130 540,110 L540,309 L0,309 Z" fill="var(--navy)"/>
      <path d="M6,162 C66,238 152,262 252,246 C304,236 374,138 534,118" fill="none" stroke="var(--white)" stroke-width="2.2"/>
      <path d="M30,190 C86,244 160,264 256,250 C310,240 380,144 528,124" fill="none" stroke="var(--white)" stroke-width="1.1" opacity=".85"/>
    </svg>

    <div class="brand">
      <div class="brand-name">Meridian Hospitality</div>
      <div class="brand-sub">Reps</div>
    </div>

    <div class="social" aria-label="Social media">
      <span class="social-dot"></span>
      <span class="social-dot"></span>
      <span class="social-dot"></span>
    </div>

    <ul class="contact">
      <li>(555) 0142-3387
        <svg class="icon" viewBox="0 0 12 12"><path d="M2.5 1 L4.5 1 L5 3.5 L3.8 4.4 C4.5 6 5.8 7.3 7.4 8 L8.4 6.9 L11 7.4 L11 9.5 C11 10.3 10.3 11 9.5 11 C5 10.7 1.3 7 1 2.5 C1 1.7 1.7 1 2.5 1 Z" fill="var(--white)"/></svg>
      </li>
      <li>name@MERIDIAN.com
        <svg class="icon" viewBox="0 0 12 12"><rect x="1" y="2.5" width="10" height="7" rx="1" fill="var(--white)"/><path d="M1.3 3 L6 6.6 L10.7 3" fill="none" stroke="var(--navy)" stroke-width="1"/></svg>
      </li>
      <li>www.MERIDIAN.com
        <svg class="icon" viewBox="0 0 12 12"><circle cx="6" cy="6" r="5" fill="var(--white)"/><ellipse cx="6" cy="6" rx="2" ry="5" fill="none" stroke="var(--navy)" stroke-width=".8"/><path d="M1 6 H11" stroke="var(--navy)" stroke-width=".8"/></svg>
      </li>
      <li class="no-icon">2170 Harbor Lane</li>
      <li class="no-icon">Glen Cove, NY 11542</li>
    </ul>

    <div class="person">
      <p class="person-name">OWEN CARTER</p>
      <p class="person-title">President</p>
    </div>
  </section>
</body>
</html>
```